A start-up named "lumerova" - a clinical research organization needs a new PowerPoint design

We need a new PowerPoint Design (incl. business card and stationery design) for an early-stage start-up named "lumerova" seeking to build an ecosystem/ strategic partner alliances or consortium of committed and active collaborators to guide important components of the clinical trial.

Our ultimate goal is to avoid false neutrals – therapies that have not been and may never be evaluated in clinical trials due to the costs and/ or complexity.

The final design should highlight our patient-centric approach, innovative study design supported with the novel AI platform to make a stronger impact on patient lives.

Please see the attached brief for more details.
Updates

Requesting the proposals on color-coding, business-card designs, clinical research visuals, and icons as well as stationery design.

Target Market(s)

Pharma/ Biotech Executives
Medical Institutions
Clinical Trial Participants (Patients)

Colors
e34398

Requirements
Must have
• Use the Color Version of purple/ magenta logo

```html
<!DOCTYPE html>
<html lang="en">
<head>
<meta charset="utf-8">
<title>lumerova — presentation system</title>
<link href="https://fonts.googleapis.com/css2?family=Montserrat:wght@400;500;600;700;800&display=swap" rel="stylesheet">
<style>
  :root{
    --violet-field:#8c51c6;
    --amber-field:#d8652c;
    --ink:#1f1f24;
    --mute:#8b8b93;
    --line:#e6e6ec;
    --white:#ffffff;
  }
  *{box-sizing:border-box;margin:0;padding:0}
  html,body{width:1200px;height:1022px;overflow:hidden}
  body{font-family:"Montserrat",Arial,sans-serif;background:#fff}
  .canvas{position:relative;width:1200px;height:1022px;overflow:hidden;
    background:linear-gradient(90deg,var(--violet-field) 0 595px,var(--amber-field) 595px 100%)}
  .theme-violet{--pri:#8a3dd1;--deep:#6b2fc0;--acc:#e2228b;--soft:#efe4fb}
  .theme-amber{--pri:#f2701f;--deep:#e4461f;--acc:#f2701f;--soft:#fde8da}

  .slide{position:absolute;width:281px;height:158px;overflow:hidden;background:var(--white)}
  .slide svg{display:block;width:281px;height:158px}
  .col-1{left:12px}.col-2{left:299px}.col-3{left:607px}.col-4{left:899px}
  .row-1{top:12px}.row-2{top:178px}.row-3{top:345px}.row-4{top:511px}.row-5{top:677px}.row-6{top:845px}

  .f-pri{fill:var(--pri)}.f-deep{fill:var(--deep)}.f-acc{fill:var(--acc)}
  .f-ink{fill:var(--ink)}.f-mute{fill:var(--mute)}.f-w{fill:#fff}.f-soft{fill:var(--soft)}
  .s-pri{stroke:var(--pri);fill:none}.s-w{stroke:#fff;fill:none}
  .s-line{stroke:var(--line);fill:#fff}
  .x-head{font-weight:800}.x-bold{font-weight:700}.x-semi{font-weight:600}
  .ph-cool{fill:#dfe3ea}.ph-warm{fill:#eae4df}
</style>
</head>
<body>
<svg width="0" height="0" style="position:absolute" aria-hidden="true">
  <defs>
    <linearGradient id="gradViolet" x1="0" y1="0" x2="1" y2="1"><stop offset="0" stop-color="#b33fd6"/><stop offset="1" stop-color="#3d66dc"/></linearGradient>
    <linearGradient id="gradVioletBand" x1="0" y1="0" x2="1" y2="0"><stop offset="0" stop-color="#9a3fd6"/><stop offset="1" stop-color="#5a52de"/></linearGradient>
    <linearGradient id="gradAmber" x1="0" y1="0" x2="1" y2="1"><stop offset="0" stop-color="#f7a43e"/><stop offset="1" stop-color="#e2501f"/></linearGradient>
    <linearGradient id="gradAmberBand" x1="0" y1="0" x2="1" y2="0"><stop offset="0" stop-color="#f59a38"/><stop offset="1" stop-color="#e55a20"/></linearGradient>
    <linearGradient id="gradPhoto" x1="0" y1="0" x2="1" y2="1"><stop offset="0" stop-color="#eef1f5"/><stop offset="1" stop-color="#c9d0da"/></linearGradient>
    <pattern id="logoCell" width="27.5" height="15.5" patternUnits="userSpaceOnUse"><rect x="3" y="4" width="21" height="7.5" rx="2" fill="#d8d8de"/></pattern>
  </defs>
</svg>

<main class="canvas">

<!-- ============ VIOLET SET ============ -->

<section class="slide cover theme-violet col-1 row-1">
  <svg viewBox="0 0 281 158">
    <rect width="281" height="158" fill="url(#gradViolet)" role="img" aria-label="Soft violet-to-blue field with a faint molecular network"/>
    <text x="95" y="87" class="f-w x-bold" font-size="18">lumerova</text>
    <rect x="184" y="70" width="8" height="8" class="f-w"/>
  </svg>
</section>

<section class="slide process theme-violet col-2 row-1">
  <svg viewBox="0 0 281 158">
    <text x="140.5" y="20" text-anchor="middle" class="x-head" font-size="7.6"><tspan class="f-acc">NEW DRUG</tspan><tspan class="f-ink"> DEVELOPMENT PROCESS</tspan></text>
    <g class="f-pri">
      <polygon points="26,37 64,37 70,45 64,53 26,53 31,45"/>
      <polygon points="72,37 110,37 116,45 110,53 72,53 77,45"/>
      <polygon points="118,37 156,37 162,45 156,53 118,53 123,45"/>
      <polygon points="164,37 202,37 208,45 202,53 164,53 169,45"/>
      <polygon points="210,37 248,37 254,45 248,53 210,53 215,45"/>
    </g>
    <g class="f-w x-bold" font-size="2.6" text-anchor="middle">
      <text x="48" y="44">PRECOMMERCIAL-</text><text x="48" y="47.5">IZATION</text>
      <text x="94" y="46">CLINICAL TRAILS</text>
      <text x="140" y="46">COMMERCIALIZATION</text>
      <text x="186" y="44">DRUGS DISCOVERY</text><text x="186" y="47.5">AND LAB RESEARCH</text>
      <text x="232" y="44">PRECLINICAL</text><text x="232" y="47.5">TESTING</text>
    </g>
    <g class="s-pri" stroke-width="0.7">
      <line x1="48" y1="53" x2="48" y2="72"/><line x1="94" y1="53" x2="94" y2="72"/><line x1="140" y1="53" x2="140" y2="72"/><line x1="186" y1="53" x2="186" y2="72"/><line x1="232" y1="53" x2="232" y2="72"/>
      <circle cx="48" cy="85" r="13" fill="#fff"/><circle cx="94" cy="85" r="13" fill="#fff"/><circle cx="140" cy="85" r="13" fill="#fff"/><circle cx="186" cy="85" r="13" fill="#fff"/><circle cx="232" cy="85" r="13" fill="#fff"/>
      <rect x="44" y="81" width="8" height="8" rx="1.5"/>
      <path d="M92 79 h4 M93 79 v4 l-3 6 h8 l-3 -6 v-4"/>
      <path d="M135 83 l8 -4 v12 l-8 -4 z"/>
      <path d="M183 79 h6 v8 h-6 z M181 91 h10"/>
      <path d="M230 79 h4 M231 79 v4 l-3 6 h8 l-3 -6 v-4"/>
    </g>
    <g font-size="2.6" text-anchor="middle">
      <text x="48" y="106" class="f-mute">1 Approved drug</text>
      <text x="94" y="106" class="f-mute">Phases I, II, III</text>
      <text x="94" y="112" class="f-acc x-semi" font-size="4.4">1, 120-5,600</text>
      <text x="94" y="116" class="f-mute">Human test subjects</text>
      <text x="186" y="109" class="f-acc x-semi" font-size="4.4">5,000-10,000</text>
      <text x="186" y="113" class="f-mute">Potential drugs</text>
      <text x="232" y="109" class="f-acc x-semi" font-size="4.4">250-300</text>
      <text x="232" y="113" class="f-mute">Potential drugs</text>
    </g>
    <rect y="124" width="281" height="34" fill="url(#gradVioletBand)"/>
    <line x1="0" y1="131" x2="281" y2="131" class="s-w" stroke-width="0.5" stroke-dasharray="1.5 1.5"/>
    <g class="f-w"><circle cx="48" cy="131" r="1.8"/><circle cx="107" cy="131" r="1.8"/><circle cx="151" cy="131" r="1.8"/><polygon points="193,129 198,129 195.5,132"/></g>
    <g class="f-w">
      <text x="45" y="143" font-size="6.5" class="x-semi">70%</text>
      <text x="45" y="147" font-size="2.5">Of potential participants &gt; 2</text>
      <text x="45" y="150" font-size="2.5">hrs away from the closest</text>
      <text x="45" y="153" font-size="2.5">clinical trial site/ study center</text>
      <text x="104" y="143" font-size="6.5" class="x-semi">67%</text>
      <text x="104" y="147" font-size="2.5">Of sites fail to meet</text>
      <text x="104" y="150" font-size="2.5">enrolment goals</text>
      <text x="148" y="143" font-size="6.5" class="x-semi">30%</text>
      <text x="148" y="147" font-size="2.5">Average drop out rate</text>
      <text x="191" y="143" font-size="6.5" class="x-semi">85%</text>
      <text x="191" y="147" font-size="2.5" class="x-bold">OF CLINICAL TRIALS</text>
      <text x="191" y="150" font-size="2.5" class="x-bold">FAIL TO RETAIN ENOUGH</text>
      <text x="191" y="153" font-size="2.5" class="x-bold">PATIENTS</text>
    </g>
  </svg>
</section>

<section class="slide why-cards theme-violet col-1 row-2">
  <svg viewBox="0 0 281 158">
    <rect y="15" width="281" height="82" fill="url(#gradVioletBand)"/>
    <rect y="6" width="80" height="91" fill="url(#gradPhoto)" role="img" aria-label="Photo of a smiling female doctor with stethoscope"/>
    <g class="f-w x-head" font-size="9"><text x="84" y="37">WHY DON’T PATIENTS</text><text x="84" y="49">ENROL IN TRIALS?</text></g>
    <g class="f-w" font-size="2.8"><text x="84" y="58">Reasons for not enrolling in a</text><text x="84" y="62">clinical trial, view of patients</text></g>
    <g class="s-line" stroke-width="0.6"><rect x="85" y="74" width="47" height="72" rx="1.5"/><rect x="143" y="74" width="47" height="72" rx="1.5"/><rect x="201" y="74" width="47" height="72" rx="1.5"/></g>
    <g class="s-pri" stroke-width="0.8">
      <circle cx="108.5" cy="89" r="4"/><path d="M108.5 93 v4"/>
      <rect x="160" y="86" width="13" height="7" rx="2"/><path d="M162 86 l2 -3 h5 l2 3"/>
      <rect x="220" y="83" width="9" height="11"/><path d="M222 86 h5 M222 89 h5 M222 92 h5"/>
    </g>
    <g text-anchor="middle">
      <g class="f-ink x-bold" font-size="3"><text x="108.5" y="109">TRUST</text><text x="166.5" y="109">UNDERSTANDING</text><text x="224.5" y="109">CONVENIENCE</text></g>
      <g class="f-ink x-bold" font-size="7.5"><text x="108.5" y="120">67%</text><text x="166.5" y="120">66%</text><text x="224.5" y="120">56%</text></g>
      <g class="f-mute" font-size="2.6"><text x="108.5" y="127">Insufficient</text><text x="108.5" y="130">staff time</text><text x="166.5" y="127">Length and</text><text x="166.5" y="130">complexity of</text><text x="166.5" y="133">constent forms</text><text x="224.5" y="127">Transportation</text><text x="224.5" y="130">to trials visits</text></g>
    </g>
  </svg>
</section>

<section class="slide why-arc theme-violet col-2 row-2">
  <svg viewBox="0 0 281 158">
    <text x="18" y="23" class="f-pri x-bold" font-size="6.5">lumerova</text><rect x="50" y="16" width="3.5" height="3.5" class="f-pri"/>
    <g class="f-ink x-head" font-size="9.2"><text x="18" y="92">WHY DON’T</text><text x="18" y="104">PATIENTS</text><text x="18" y="116">ENROL IN TRIALS?</text></g>
    <line x1="18" y1="121" x2="85" y2="121" class="s-pri" stroke-width="0.5"/>
    <g class="f-ink" font-size="2.8"><text x="18" y="130">Reasons for not enrolling in a</text><text x="18" y="134">clinical trial, view of patients</text></g>
    <g class="s-pri" stroke-width="38" style="stroke:var(--pri)">
      <path d="M118.2 97.9 A65 65 0 0 1 149.5 60.6"/>
      <path d="M154.6 58.1 A65 65 0 0 1 205.4 58.1"/>
      <path d="M210.5 60.6 A65 65 0 0 1 241.8 97.9"/>
    </g>
    <g class="f-w x-bold" font-size="5.5"><text x="121" y="88">67%</text><text x="166" y="51">66%</text><text x="230" y="82">56%</text></g>
    <g class="f-w x-bold" font-size="2.6"><text x="133" y="70">TRUST</text><text x="184" y="44">UNDER-</text><text x="184" y="47.5">STANDING</text><text x="218" y="64">CONVENIENCE</text></g>
    <rect x="170" y="72" width="22" height="82" rx="8" fill="url(#gradPhoto)" role="img" aria-label="Illustration of a doctor in a white coat presenting"/>
  </svg>
</section>

<section class="slide audience-ring theme-violet col-1 row-3">
  <svg viewBox="0 0 281 158">
    <text x="140.5" y="18" text-anchor="middle" class="x-head" font-size="7.5"><tspan class="f-acc">TARGET</tspan><tspan class="f-ink"> AUDIENCE</tspan></text>
    <rect x="115" y="60" width="48" height="48" transform="rotate(45 139 84)" fill="none" style="stroke:var(--pri)" stroke-width="12"/>
    <g class="f-w"><circle cx="139" cy="50" r="5"/><circle cx="104" cy="84" r="5"/><circle cx="174" cy="84" r="5"/><circle cx="139" cy="118" r="5"/></g>
    <g class="f-pri"><circle cx="139" cy="50" r="3"/><circle cx="104" cy="84" r="3"/><circle cx="174" cy="84" r="3"/><circle cx="139" cy="118" r="3"/></g>
    <text x="139" y="86" text-anchor="middle" class="f-acc x-bold" font-size="6">REQUEST</text>
    <g class="f-ink x-bold" font-size="3" text-anchor="middle"><text x="139" y="33">Participants/</text><text x="139" y="37">Patients</text><text x="139" y="132">Lumerova</text></g>
    <g class="f-ink x-bold" font-size="3"><text x="58" y="84">Pharmaceutical/</text><text x="58" y="88">Biotech Companies</text><text x="190" y="84">Medical</text><text x="190" y="88">Institutions/Hospitals</text></g>
    <g class="f-mute" font-size="2.8"><text x="84" y="56">Drug</text><text x="76" y="60">Candidates</text><text x="185" y="56">Implementation</text><text x="185" y="60">of clinical trails</text><text x="86" y="115">CRO</text><text x="84" y="119">Services</text><text x="185" y="115">SMO</text><text x="185" y="119">Services</text></g>
  </svg>
</section>

<section class="slide brand theme-violet col-2 row-3">
  <svg viewBox="0 0 281 158">
    <text x="26" y="62" class="f-pri x-bold" font-size="6.5">lumerova</text><rect x="58" y="55" width="3.5" height="3.5" class="f-pri"/>
    <text x="26" y="82" class="f-acc x-head" font-size="13">BRAND</text>
    <text x="26" y="100" class="f-ink x-head" font-size="13">PERSONALITY</text>
    <g role="img" aria-label="Collage of clinical research photos: DNA, lab microscopes, doctors, cells">
      <path d="M185 55 L215 52 L233 58 M170 65 L196 80 L230 72 M196 80 L205 105 L230 92 M205 105 L215 122" class="s-pri" stroke-width="1"/>
      <rect x="156" y="54" width="30" height="30" rx="2" fill="#3a6fd6"/>
      <rect x="190" y="40" width="20" height="20" rx="2" class="ph-cool"/>
      <rect x="218" y="43" width="20" height="20" rx="2" fill="#5b83c9"/>
      <rect x="200" y="66" width="16" height="16" rx="2" class="ph-cool"/>
      <rect x="224" y="62" width="18" height="18" rx="2" fill="#2f8fd8"/>
      <rect x="194" y="98" width="24" height="24" rx="2" fill="#8aa6c6"/>
      <rect x="226" y="96" width="16" height="16" rx="2" fill="#3c5fc4"/>
      <rect x="172" y="44" width="8" height="8" rx="1" fill="#2a4fa8"/>
      <rect x="248" y="57" width="7" height="7" rx="1" class="ph-cool"/>
      <rect x="249" y="85" width="8" height="8" rx="1" class="ph-cool"/>
      <rect x="240" y="120" width="7" height="7" rx="1" class="ph-cool"/>
      <rect x="218" y="128" width="9" height="9" rx="1" fill="#6d8ec0"/>
    </g>
  </svg>
</section>

<section class="slide organisation theme-violet col-1 row-4">
  <svg viewBox="0 0 281 158">
    <rect x="198" width="83" height="158" class="f-pri"/>
    <circle cx="210" cy="80" r="50" fill="#fff"/>
    <circle cx="210" cy="80" r="47" fill="url(#gradPhoto)" role="img" aria-label="Photo of a researcher at a microscope"/>
    <text x="21" y="22" class="f-acc x-head" font-size="9.5">ORGANISATION</text>
    <text x="21" y="34" class="f-ink x-head" font-size="9.5">WHO WE ARE</text>
    <g class="f-ink" font-size="2.8"><text x="21" y="45">LUMEROVA is an early-stage start-up seeking to build an ecosystem/</text><text x="21" y="49">strategic partner alliances or consortium of committed and active</text><text x="21" y="53">collaborators to guide important components of the clinical trial</text></g>
    <g class="f-pri"><rect x="21" y="68" width="12" height="12"/><rect x="21" y="88" width="12" height="12"/><rect x="21" y="108" width="12" height="12"/></g>
    <g class="s-w" stroke-width="0.7"><circle cx="27" cy="74" r="3"/><circle cx="27" cy="94" r="3"/><circle cx="27" cy="114" r="3"/></g>
    <g class="f-mute" font-size="2.4">
      <text x="37" y="71">The Science around new medical treatments is rapidly</text><text x="37" y="74">progressing, but there are many questions surround-</text><text x="37" y="77">ing how Science could Translate into a Therapy</text>
      <text x="37" y="91">Success lies in moving from an idea generating phase at</text><text x="37" y="94">a 50,000-foot level to the on-the ground implementa-</text><text x="37" y="97">tion phase, scientifically valuable and operationally feasible</text>
      <text x="37" y="111">We have no time or money to spend on wasted efforts.</text><text x="37" y="114">We really need to focus on tasks where patients</text><text x="37" y="117">could gain something and avoid type I error</text>
    </g>
    <text x="18" y="141" class="f-ink x-bold" font-size="3.4">...therefore, we strive to work with lumerova (for sapiens)</text>
  </svg>
</section>

<section class="slide audience-cross theme-violet col-2 row-4">
  <svg viewBox="0 0 281 158">
    <text x="10" y="22" class="f-pri x-bold" font-size="6.5">lumerova</text><rect x="42" y="15" width="3.5" height="3.5" class="f-pri"/>
    <text x="140.5" y="22" text-anchor="middle" class="x-head" font-size="7.5"><tspan class="f-acc">TARGET</tspan><tspan class="f-ink"> AUDIENCE</tspan></text>
    <g class="f-pri"><rect x="124" y="58" width="27" height="24"/><rect x="124" y="103" width="27" height="24"/><rect x="99" y="80" width="27" height="24"/></g>
    <rect x="149" y="80" width="27" height="24" class="f-soft"/>
    <circle cx="137.5" cy="92" r="13" class="f-w"/>
    <text x="137.5" y="93.5" text-anchor="middle" class="f-ink x-bold" font-size="3.4">REQUEST</text>
    <g class="s-w" stroke-width="1"><path d="M133 68 l4.5 4 4.5 -4 a2.5 2.5 0 0 0 -4.5 -2 a2.5 2.5 0 0 0 -4.5 2z"/><path d="M108 95 l8 -8"/><path d="M158 93 l4.5 -4 4.5 4 v5 h-9z"/><rect x="133" y="111" width="8" height="8"/></g>
    <g class="f-ink x-bold" font-size="3" text-anchor="middle"><text x="137.5" y="44">Participants/ Patients</text><text x="137.5" y="141">Lumerova</text></g>
    <g class="f-ink x-bold" font-size="3"><text x="58" y="91">Pharmaceutical/</text><text x="58" y="95">Biotech Companies</text><text x="181" y="91">Medical</text><text x="181" y="95">Institutions/Hospitals</text></g>
    <g class="f-mute" font-size="2.8"><text x="100" y="67">Drug</text><text x="90" y="71">Candidates</text><text x="169" y="64">Implementation</text><text x="169" y="68">of clinical trails</text><text x="100" y="117">CRO</text><text x="97" y="121">Services</text><text x="169" y="117">SMO</text><text x="169" y="121">Services</text></g>
  </svg>
</section>

<section class="slide divider theme-violet col-1 row-5">
  <svg viewBox="0 0 281 158">
    <rect width="281" height="158" fill="url(#gradViolet)" role="img" aria-label="Violet-blue field with faint DNA helix"/>
    <g class="f-w x-head" font-size="13"><text x="74" y="74">ORGANISATION &amp;</text><text x="74" y="92">TARGET AUDIENCE</text></g>
  </svg>
</section>

<section class="slide challenge theme-violet col-2 row-5">
  <svg viewBox="0 0 281 158">
    <rect x="110" width="171" height="158" fill="url(#gradPhoto)" role="img" aria-label="Photo of a smiling elderly patient in a hospital bed"/>
    <text x="24" y="70" class="f-acc x-head" font-size="16">CHALLENGE</text>
    <text x="24" y="92" class="f-ink x-head" font-size="16">UNMET NEED</text>
  </svg>
</section>

<section class="slide process-circle theme-violet col-1 row-6">
  <svg viewBox="0 0 281 158">
    <rect x="197" width="84" height="158" fill="url(#gradViolet)"/>
    <circle cx="100" cy="80" r="42" class="s-pri" stroke-width="0.5" stroke-dasharray="1.5 1.5"/>
    <rect x="82" y="56" width="36" height="96" rx="10" fill="url(#gradPhoto)" role="img" aria-label="Hand touching a digital interface"/>
    <g class="f-pri"><circle cx="100" cy="38" r="7"/><circle cx="63" cy="53" r="7"/><circle cx="137" cy="53" r="7"/></g>
    <g fill="#fff" class="s-pri" stroke-width="0.6"><circle cx="65" cy="96" r="7"/><circle cx="135" cy="96" r="7"/></g>
    <g class="f-ink x-bold" font-size="3"><text x="100" y="18" text-anchor="middle">COMMERCIALIZATION</text><text x="23" y="50">PRECOMMER-</text><text x="23" y="54">CIALIZATION</text><text x="31" y="80">CLINICAL</text><text x="34" y="84">TRAILS</text><text x="147" y="45">DRUGS DISCOVERY</text><text x="147" y="49">AND LAB RESEARCH</text><text x="147" y="81">PRECLINICAL</text><text x="147" y="85">TESTING</text></g>
    <g class="f-acc x-semi" font-size="4.5"><text x="18" y="93">1, 120-5,600</text><text x="147" y="58">5,000-10,000</text><text x="147" y="93">250-300</text></g>
    <g class="f-mute" font-size="2.4"><text x="23" y="60">1 Approved drug</text><text x="24" y="97">Human test subjects</text><text x="147" y="62">Potential drugs</text><text x="147" y="97">Potential drugs</text></g>
    <text x="19" y="146" class="f-pri x-bold" font-size="6.5">lumerova</text><rect x="51" y="139" width="3.5" height="3.5" class="f-pri"/>
    <g class="f-w x-head" font-size="5.5"><text x="211" y="17">NEW DRUG</text><text x="211" y="24.5">DEVELOPMENT</text><text x="211" y="32">PROCESS</text></g>
    <line x1="207" y1="40" x2="207" y2="150" class="s-w" stroke-width="0.4" stroke-dasharray="1 1.5"/>
    <g class="f-w">
      <text x="211" y="55" font-size="6.5" class="x-semi">70%</text><text x="211" y="59" font-size="2.4">Of potential participants &gt; 2</text><text x="211" y="62" font-size="2.4">hrs away from the closest</text><text x="211" y="65" font-size="2.4">clinical trial site/ study center</text>
      <text x="211" y="81" font-size="6.5" class="x-semi">67%</text><text x="211" y="85" font-size="2.4">Of sites fail to meet</text><text x="211" y="88" font-size="2.4">enrolment goals</text>
      <text x="211" y="104" font-size="6.5" class="x-semi">30%</text><text x="211" y="108" font-size="2.4">Average drop out rate</text>
      <text x="211" y="127" font-size="6.5" class="x-semi">85%</text><text x="211" y="132" font-size="2.6" class="x-bold">OF CLINICAL TRIALS</text><text x="211" y="135.5" font-size="2.6" class="x-bold">FAIL TO RETAIN ENOUGH</text><text x="211" y="139" font-size="2.6" class="x-bold">PATIENTS</text>
    </g>
  </svg>
</section>

<section class="slide competition theme-violet col-2 row-6">
  <svg viewBox="0 0 281 158">
    <rect x="200" width="81" height="158" class="f-pri"/>
    <rect x="14" y="36" width="248" height="112" fill="#fff"/>
    <text x="14" y="21" class="f-ink x-head" font-size="10">COMPETITION LOGOS</text>
    <text x="14" y="28" class="f-ink" font-size="3.3">Clinical Research Organizations (CROs)</text>
    <text x="225" y="21" class="f-w x-bold" font-size="6.5">lumerova</text><rect x="257" y="14" width="3.5" height="3.5" class="f-w"/>
    <rect x="14" y="38" width="247.5" height="108.5" fill="url(#logoCell)" role="img" aria-label="Grid of competitor CRO marks"/>
  </svg>
</section>

<!-- ============ AMBER SET ============ -->

<section class="slide cover theme-amber col-3 row-1">
  <svg viewBox="0 0 281 158">
    <rect width="281" height="158" fill="url(#gradAmber)" role="img" aria-label="Warm orange field with a faint molecular network"/>
    <text x="95" y="87" class="f-w x-bold" font-size="18">lumerova</text>
    <rect x="184" y="70" width="8" height="8" class="f-w"/>
  </svg>
</section>

<section class="slide organisation-banner theme-amber col-4 row-1">
  <svg viewBox="0 0 281 158">
    <rect x="165" width="116" height="158" fill="url(#gradPhoto)" role="img" aria-label="Photo of a doctor with a family and tablet"/>
    <text x="13" y="22" class="x-head" font-size="9.5"><tspan class="f-acc">ORGANISATION</tspan><tspan class="f-ink"> WHO WE ARE</tspan></text>
    <polygon points="0,32 168,32 146,62 0,62" fill="url(#gradAmberBand)"/>
    <g class="f-w" font-size="2.8"><text x="25" y="43">LUMEROVA is an early-stage start-up seeking to build an ecosystem/</text><text x="25" y="47">strategic partner alliances or consortium of committed and active</text><text x="25" y="51">collaborators to guide important components of the clinical trial</text></g>
    <g><circle cx="29" cy="83" r="7" fill="#c4122f"/><circle cx="29" cy="103" r="7" fill="#e2361f"/><circle cx="29" cy="123" r="7" fill="#f08a1f"/></g>
    <g class="s-w" stroke-width="0.7"><circle cx="29" cy="83" r="3"/><circle cx="29" cy="103" r="3"/><circle cx="29" cy="123" r="3"/></g>
    <g class="f-mute" font-size="2.4">
      <text x="40" y="81">The Science around new medical treatments is rapidly</text><text x="40" y="84">progressing, but there are many questions surround-</text><text x="40" y="87">ing how Science could Translate into a Therapy</text>
      <text x="40" y="101">Success lies in moving from an idea generating phase at</text><text x="40" y="104">a 50,000-foot level to the on-the ground implementa-</text><text x="40" y="107">tion phase, scientifically valuable and operationally feasible</text>
      <text x="40" y="121">We have no time or money to spend on wasted efforts.</text><text x="40" y="124">We really need to focus on tasks where patients</text><text x="40" y="127">could gain something and avoid type I error</text>
    </g>
    <circle cx="175" cy="65" r="8" class="f-pri"/>
    <text x="14" y="146" class="f-ink x-bold" font-size="3.4">...therefore, we strive to work with lumerova (for sapiens)</text>
  </svg>
</section>

<section class="slide organisation theme-amber col-3 row-2">
  <svg viewBox="0 0 281 158">
    <rect x="198" width="83" height="158" class="f-pri"/>
    <circle cx="210" cy="80" r="50" fill="#fff"/>
    <circle cx="210" cy="80" r="47" fill="url(#gradPhoto)" role="img" aria-label="Photo of a researcher at a microscope"/>
    <text x="21" y="22" class="f-acc x-head" font-size="9.5">ORGANISATION</text>
    <text x="21" y="34" class="f-ink x-head" font-size="9.5">WHO WE ARE</text>
    <g class="f-ink" font-size="2.8"><text x="21" y="45">LUMEROVA is an early-stage start-up seeking to build an ecosystem/</text><text x="21" y="49">strategic partner alliances or consortium of committed and active</text><text x="21" y="53">collaborators to guide important components of the clinical trial</text></g>
    <g><rect x="21" y="68" width="12" height="12" fill="#c4122f"/><rect x="21" y="88" width="12" height="12" fill="#e2361f"/><rect x="21" y="108" width="12" height="12" fill="#f0601f"/></g>
    <g class="s-w" stroke-width="0.7"><circle cx="27" cy="74" r="3"/><circle cx="27" cy="94" r="3"/><circle cx="27" cy="114" r="3"/></g>
    <g class="f-mute" font-size="2.4">
      <text x="37" y="71">The Science around new medical treatments is rapidly</text><text x="37" y="74">progressing, but there are many questions surround-</text><text x="37" y="77">ing how Science could Translate into a Therapy</text>
      <text x="37" y="91">Success lies in moving from an idea generating phase at</text><text x="37" y="94">a 50,000-foot level to the on-the ground implementa-</text><text x="37" y="97">tion phase, scientifically valuable and operationally feasible</text>
      <text x="37" y="111">We have no time or money to spend on wasted efforts.</text><text x="37" y="114">We really need to focus on tasks where patients</text><text x="37" y="117">could gain something and avoid type I error</text>
    </g>
    <text x="18" y="141" class="f-ink x-bold" font-size="3.4">...therefore, we strive to work with lumerova (for sapiens)</text>
    <text x="247" y="148" class="f-w x-bold" font-size="4.5">lumerova</text>
  </svg>
</section>

<section class="slide challenge theme-amber col-4 row-2">
  <svg viewBox="0 0 281 158">
    <rect x="110" width="171" height="158" fill="url(#gradPhoto)" role="img" aria-label="Photo of a smiling elderly patient with a caregiver's hand"/>
    <text x="24" y="70" class="f-acc x-head" font-size="16">CHALLENGE</text>
    <text x="24" y="92" class="f-ink x-head" font-size="16">UNMET NEED</text>
  </svg>
</section>

<section class="slide divider theme-amber col-3 row-3">
  <svg viewBox="0 0 281 158">
    <rect width="281" height="158" fill="url(#gradAmber)" role="img" aria-label="Orange field with faint DNA helix"/>
    <g class="f-w x-head" font-size="13"><text x="74" y="74">ORGANISATION &amp;</text><text x="74" y="92">TARGET AUDIENCE</text></g>
  </svg>
</section>

<section class="slide why-cards theme-amber col-4 row-3">
  <svg viewBox="0 0 281 158">
    <rect y="15" width="281" height="82" fill="url(#gradAmberBand)"/>
    <rect y="6" width="80" height="91" fill="url(#gradPhoto)" role="img" aria-label="Photo of a smiling female doctor with stethoscope"/>
    <g class="f-w x-head" font-size="9"><text x="84" y="37">WHY DON’T PATIENTS</text><text x="84" y="49">ENROL IN TRIALS?</text></g>
    <g class="f-w" font-size="2.8"><text x="84" y="58">Reasons for not enrolling in a</text><text x="84" y="62">clinical trial, view of patients</text></g>
    <g class="s-line" stroke-width="0.6"><rect x="85" y="74" width="47" height="72" rx="1.5"/><rect x="143" y="74" width="47" height="72" rx="1.5"/><rect x="201" y="74" width="47" height="72" rx="1.5"/></g>
    <g class="s-pri" stroke-width="0.8">
      <circle cx="108.5" cy="89" r="4"/><path d="M108.5 93 v4"/>
      <rect x="160" y="86" width="13" height="7" rx="2"/><path d="M162 86 l2 -3 h5 l2 3"/>
      <rect x="220" y="83" width="9" height="11"/><path d="M222 86 h5 M222 89 h5 M222 92 h5"/>
    </g>
    <g text-anchor="middle">
      <g class="f-ink x-bold" font-size="3"><text x="108.5" y="109">TRUST</text><text x="166.5" y="109">UNDERSTANDING</text><text x="224.5" y="109">CONVENIENCE</text></g>
      <g class="f-ink x-bold" font-size="7.5"><text x="108.5" y="120">67%</text><text x="166.5" y="120">66%</text><text x="224.5" y="120">56%</text></g>
      <g class="f-mute" font-size="2.6"><text x="108.5" y="127">Insufficient</text><text x="108.5" y="130">staff time</text><text x="166.5" y="127">Length and</text><text x="166.5" y="130">complexity of</text><text x="166.5" y="133">constent forms</text><text x="224.5" y="127">Transportation</text><text x="224.5" y="130">to trials visits</text></g>
    </g>
  </svg>
</section>

<section class="slide why-arc theme-amber col-3 row-4">
  <svg viewBox="0 0 281 158">
    <text x="18" y="23" class="f-pri x-bold" font-size="6.5">lumerova</text><rect x="50" y="16" width="3.5" height="3.5" class="f-pri"/>
    <g class="f-ink x-head" font-size="9.2"><text x="18" y="92">WHY DON’T</text><text x="18" y="104">PATIENTS</text><text x="18" y="116">ENROL IN TRIALS?</text></g>
    <line x1="18" y1="121" x2="85" y2="121" class="s-pri" stroke-width="0.5"/>
    <g class="f-ink" font-size="2.8"><text x="18" y="130">Reasons for not enrolling in a</text><text x="18" y="134">clinical trial, view of patients</text></g>
    <g fill="none" stroke-width="38" style="stroke:var(--pri)">
      <path d="M118.2 97.9 A65 65 0 0 1 149.5 60.6"/>
      <path d="M154.6 58.1 A65 65 0 0 1 205.4 58.1"/>
      <path d="M210.5 60.6 A65 65 0 0 1 241.8 97.9"/>
    </g>
    <g class="f-w x-bold" font-size="5.5"><text x="121" y="88">67%</text><text x="166" y="51">66%</text><text x="230" y="82">56%</text></g>
    <g class="f-w x-bold" font-size="2.6"><text x="133" y="70">TRUST</text><text x="184" y="44">UNDER-</text><text x="184" y="47.5">STANDING</text><text x="218" y="64">CONVENIENCE</text></g>
    <rect x="170" y="72" width="22" height="82" rx="8" fill="url(#gradPhoto)" role="img" aria-label="Illustration of a doctor in a white coat presenting"/>
  </svg>
</section>

<section class="slide brand theme-amber col-4 row-4">
  <svg viewBox="0 0 281 158">
    <text x="26" y="62" class="f-pri x-bold" font-size="6.5">lumerova</text><rect x="58" y="55" width="3.5" height="3.5" class="f-pri"/>
    <text x="26" y="82" class="f-acc x-head" font-size="13">BRAND</text>
    <text x="26" y="100" class="f-ink x-head" font-size="13">PERSONALITY</text>
    <g role="img" aria-label="Collage of clinical research photos: DNA, lab microscopes, doctors, cells">
      <path d="M185 55 L215 52 L233 58 M170 65 L196 80 L230 72 M196 80 L205 105 L230 92 M205 105 L215 122" class="s-pri" stroke-width="1"/>
      <rect x="156" y="54" width="30" height="30" rx="2" fill="#3a6fd6"/>
      <rect x="190" y="40" width="20" height="20" rx="2" class="ph-cool"/>
      <rect x="218" y="43" width="20" height="20" rx="2" fill="#5b83c9"/>
      <rect x="200" y="66" width="16" height="16" rx="2" class="ph-cool"/>
      <rect x="224" y="62" width="18" height="18" rx="2" fill="#2f8fd8"/>
      <rect x="194" y="98" width="24" height="24" rx="2" fill="#8aa6c6"/>
      <rect x="226" y="96" width="16" height="16" rx="2" fill="#3c5fc4"/>
      <rect x="172" y="44" width="8" height="8" rx="1" fill="#2a4fa8"/>
      <rect x="248" y="57" width="7" height="7" rx="1" class="ph-cool"/>
      <rect x="249" y="85" width="8" height="8" rx="1" class="ph-cool"/>
      <rect x="240" y="120" width="7" height="7" rx="1" class="ph-cool"/>
      <rect x="218" y="128" width="9" height="9" rx="1" fill="#6d8ec0"/>
    </g>
  </svg>
</section>

<section class="slide process-circle theme-amber col-3 row-5">
  <svg viewBox="0 0 281 158">
    <rect x="197" width="84" height="158" fill="url(#gradAmber)"/>
    <circle cx="100" cy="80" r="42" class="s-pri" stroke-width="0.5" stroke-dasharray="1.5 1.5"/>
    <rect x="82" y="56" width="36" height="96" rx="10" fill="url(#gradPhoto)" role="img" aria-label="Hand touching a digital interface"/>
    <g class="f-pri"><circle cx="63" cy="53" r="7"/><circle cx="137" cy="53" r="7"/></g>
    <g fill="#fff" class="s-pri" stroke-width="0.6"><circle cx="100" cy="38" r="7"/><circle cx="65" cy="96" r="7"/><circle cx="135" cy="96" r="7"/></g>
    <g class="f-ink x-bold" font-size="3"><text x="100" y="18" text-anchor="middle">COMMERCIALIZATION</text><text x="23" y="50">PRECOMMER-</text><text x="23" y="54">CIALIZATION</text><text x="31" y="80">CLINICAL</text><text x="34" y="84">TRAILS</text><text x="147" y="45">DRUGS DISCOVERY</text><text x="147" y="49">AND LAB RESEARCH</text><text x="147" y="81">PRECLINICAL</text><text x="147" y="85">TESTING</text></g>
    <g class="f-acc x-semi" font-size="4.5"><text x="18" y="93">1, 120-5,600</text><text x="147" y="58">5,000-10,000</text><text x="147" y="93">250-300</text></g>
    <g class="f-mute" font-size="2.4"><text x="23" y="60">1 Approved drug</text><text x="24" y="97">Human test subjects</text><text x="147" y="62">Potential drugs</text><text x="147" y="97">Potential drugs</text></g>
    <text x="19" y="146" class="f-pri x-bold" font-size="6.5">lumerova</text><rect x="51" y="139" width="3.5" height="3.5" class="f-pri"/>
    <g class="f-w x-head" font-size="5.5"><text x="211" y="17">NEW DRUG</text><text x="211" y="24.5">DEVELOPMENT</text><text x="211" y="32">PROCESS</text></g>
    <line x1="207" y1="40" x2="207" y2="150" class="s-w" stroke-width="0.4" stroke-dasharray="1 1.5"/>
    <g class="f-w">
      <text x="211" y="55" font-size="6.5" class="x-semi">70%</text><text x="211" y="59" font-size="2.4">Of potential participants &gt; 2</text><text x="211" y="62" font-size="2.4">hrs away from the closest</text><text x="211" y="65" font-size="2.4">clinical trial site/ study center</text>
      <text x="211" y="81" font-size="6.5" class="x-semi">67%</text><text x="211" y="85" font-size="2.4">Of sites fail to meet</text><text x="211" y="88" font-size="2.4">enrolment goals</text>
      <text x="211" y="104" font-size="6.5" class="x-semi">30%</text><text x="211" y="108" font-size="2.4">Average drop out rate</text>
      <text x="211" y="127" font-size="6.5" class="x-semi">85%</text><text x="211" y="132" font-size="2.6" class="x-bold">OF CLINICAL TRIALS</text><text x="211" y="135.5" font-size="2.6" class="x-bold">FAIL TO RETAIN ENOUGH</text><text x="211" y="139" font-size="2.6" class="x-bold">PATIENTS</text>
    </g>
  </svg>
</section>

<section class="slide process theme-amber col-4 row-5">
  <svg viewBox="0 0 281 158">
    <text x="140.5" y="20" text-anchor="middle" class="x-head" font-size="7.6"><tspan class="f-acc">NEW DRUG</tspan><tspan class="f-ink"> DEVELOPMENT PROCESS</tspan></text>
    <polygon points="26,37 64,37 70,45 64,53 26,53 31,45" fill="#f59a38"/>
    <polygon points="72,37 110,37 116,45 110,53 72,53 77,45" fill="#f2801f"/>
    <polygon points="118,37 156,37 162,45 156,53 118,53 123,45" fill="#ea5a1f"/>
    <polygon points="164,37 202,37 208,45 202,53 164,53 169,45" fill="#d7262a"/>
    <polygon points="210,37 248,37 254,45 248,53 210,53 215,45" fill="#a5185e"/>
    <g class="f-w x-bold" font-size="2.6" text-anchor="middle">
      <text x="48" y="44">PRECOMMERCIAL-</text><text x="48" y="47.5">IZATION</text>
      <text x="94" y="46">CLINICAL TRAILS</text>
      <text x="140" y="46">COMMERCIALIZATION</text>
      <text x="186" y="44">DRUGS DISCOVERY</text><text x="186" y="47.5">AND LAB RESEARCH</text>
      <text x="232" y="44">PRECLINICAL</text><text x="232" y="47.5">TESTING</text>
    </g>
    <g class="s-pri" stroke-width="0.7">
      <line x1="48" y1="53" x2="48" y2="72"/><line x1="94" y1="53" x2="94" y2="72"/><line x1="140" y1="53" x2="140" y2="72"/><line x1="186" y1="53" x2="186" y2="72"/><line x1="232" y1="53" x2="232" y2="72"/>
      <circle cx="48" cy="85" r="13" fill="#fff"/><circle cx="94" cy="85" r="13" fill="#fff"/><circle cx="140" cy="85" r="13" fill="#fff"/><circle cx="186" cy="85" r="13" fill="#fff"/><circle cx="232" cy="85" r="13" fill="#fff"/>
      <rect x="44" y="81" width="8" height="8" rx="1.5"/>
      <path d="M92 79 h4 M93 79 v4 l-3 6 h8 l-3 -6 v-4"/>
      <path d="M135 83 l8 -4 v12 l-8 -4 z"/>
      <path d="M183 79 h6 v8 h-6 z M181 91 h10"/>
      <path d="M230 79 h4 M231 79 v4 l-3 6 h8 l-3 -6 v-4"/>
    </g>
    <g font-size="2.6" text-anchor="middle">
      <text x="48" y="106" class="f-mute">1 Approved drug</text>
      <text x="94" y="106" class="f-mute">Phases I, II, III</text>
      <text x="94" y="112" class="f-acc x-semi" font-size="4.4">1, 120-5,600</text>
      <text x="94" y="116" class="f-mute">Human test subjects</text>
      <text x="186" y="109" class="f-acc x-semi" font-size="4.4">5,000-10,000</text>
      <text x="186" y="113" class="f-mute">Potential drugs</text>
      <text x="232" y="109" class="f-acc x-semi" font-size="4.4">250-300</text>
      <text x="232" y="113" class="f-mute">Potential drugs</text>
    </g>
    <rect y="124" width="281" height="34" fill="url(#gradAmberBand)"/>
    <line x1="0" y1="131" x2="281" y2="131" class="s-w" stroke-width="0.5" stroke-dasharray="1.5 1.5"/>
    <g class="f-w"><circle cx="48" cy="131" r="1.8"/><circle cx="107" cy="131" r="1.8"/><circle cx="151" cy="131" r="1.8"/><polygon points="193,129 198,129 195.5,132"/></g>
    <g class="f-w">
      <text x="45" y="143" font-size="6.5" class="x-semi">70%</text>
      <text x="45" y="147" font-size="2.5">Of potential participants &gt; 2</text>
      <text x="45" y="150" font-size="2.5">hrs away from the closest</text>
      <text x="45" y="153" font-size="2.5">clinical trial site/ study center</text>
      <text x="104" y="143" font-size="6.5" class="x-semi">67%</text>
      <text x="104" y="147" font-size="2.5">Of sites fail to meet</text>
      <text x="104" y="150" font-size="2.5">enrolment goals</text>
      <text x="148" y="143" font-size="6.5" class="x-semi">30%</text>
      <text x="148" y="147" font-size="2.5">Average drop out rate</text>
      <text x="191" y="143" font-size="6.5" class="x-semi">85%</text>
      <text x="191" y="147" font-size="2.5" class="x-bold">OF CLINICAL TRIALS</text>
      <text x="191" y="150" font-size="2.5" class="x-bold">FAIL TO RETAIN ENOUGH</text>
      <text x="191" y="153" font-size="2.5" class="x-bold">PATIENTS</text>
    </g>
  </svg>
</section>

<section class="slide competition theme-amber col-3 row-6">
  <svg viewBox="0 0 281 158">
    <rect x="200" width="81" height="158" class="f-pri"/>
    <rect x="14" y="36" width="248" height="112" fill="#fff"/>
    <text x="14" y="21" class="f-ink x-head" font-size="10">COMPETITION LOGOS</text>
    <text x="14" y="28" class="f-ink" font-size="3.3">Clinical Research Organizations (CROs)</text>
    <text x="225" y="21" class="f-w x-bold" font-size="6.5">lumerova</text><rect x="257" y="14" width="3.5" height="3.5" class="f-w"/>
    <rect x="14" y="38" width="247.5" height="108.5" fill="url(#logoCell)" role="img" aria-label="Grid of competitor CRO marks"/>
  </svg>
</section>

<section class="slide audience-cross theme-amber col-4 row-6">
  <svg viewBox="0 0 281 158">
    <text x="10" y="22" class="f-pri x-bold" font-size="6.5">lumerova</text><rect x="42" y="15" width="3.5" height="3.5" class="f-pri"/>
    <text x="140.5" y="22" text-anchor="middle" class="x-head" font-size="7.5"><tspan class="f-acc">TARGET</tspan><tspan class="f-ink"> AUDIENCE</tspan></text>
    <rect x="124" y="58" width="27" height="24" fill="#c4124a"/>
    <rect x="124" y="103" width="27" height="24" fill="#e2361f"/>
    <rect x="99" y="80" width="27" height="24" fill="#d7262a"/>
    <rect x="149" y="80" width="27" height="24" class="f-pri"/>
    <circle cx="137.5" cy="92" r="13" class="f-w"/>
    <text x="137.5" y="93.5" text-anchor="middle" class="f-ink x-bold" font-size="3.4">REQUEST</text>
    <g class="s-w" stroke-width="1"><path d="M133 68 l4.5 4 4.5 -4 a2.5 2.5 0 0 0 -4.5 -2 a2.5 2.5 0 0 0 -4.5 2z"/><path d="M108 95 l8 -8"/><path d="M158 93 l4.5 -4 4.5 4 v5 h-9z"/><rect x="133" y="111" width="8" height="8"/></g>
    <g class="f-ink x-bold" font-size="3" text-anchor="middle"><text x="137.5" y="44">Participants/ Patients</text><text x="137.5" y="141">Lumerova</text></g>
    <g class="f-ink x-bold" font-size="3"><text x="58" y="91">Pharmaceutical/</text><text x="58" y="95">Biotech Companies</text><text x="181" y="91">Medical</text><text x="181" y="95">Institutions/Hospitals</text></g>
    <g class="f-mute" font-size="2.8"><text x="100" y="67">Drug</text><text x="90" y="71">Candidates</text><text x="169" y="64">Implementation</text><text x="169" y="68">of clinical trails</text><text x="100" y="117">CRO</text><text x="97" y="121">Services</text><text x="169" y="117">SMO</text><text x="169" y="121">Services</text></g>
  </svg>
</section>

</main>
</body>
</html>
```